The Plate Compass

Cutting Through the Noise to What Actually Works.

Nutrition book

Target Market(s)

People looking to be or get healthy and eat right.

```html
<!DOCTYPE html>
<html lang="en">
<head>
<meta charset="utf-8">
<title>The Plate Compass — Cover</title>
<link rel="stylesheet" href="https://fonts.googleapis.com/css2?family=Playfair+Display:wght@700;800&family=Poppins:wght@600;700&display=swap">
<style>
  :root {
    --backdrop: #9c9c9c;
    --paper: #f5f4f2;
    --paper-edge: #e9e8e5;
    --green: #3d7320;
    --orange: #e07408;
    --ink: #1f2a24;
    --rule: #7a7a7a;
    --noise: #a3a1a1;
    --supplements: #e9c000;
    --timing: #e07408;
    --quality: #c21124;
    --protein: #7a38b7;
    --calories: #3d7320;
    --plate-light: #ffffff;
    --plate-mid: #e7ded2;
    --plate-food: #c9854a;
  }
  html, body {
    margin: 0;
    width: 1200px;
    height: 2385px;
    overflow: hidden;
    background: var(--backdrop);
  }
  .cover {
    position: absolute;
    left: 40px;
    top: 352px;
    width: 701px;
    height: 1052px;
    transform: scale(1.5977);
    transform-origin: 0 0;
    overflow: hidden;
    background: linear-gradient(90deg, var(--paper-edge), var(--paper) 20%, var(--paper) 80%, var(--paper-edge));
    box-shadow: 0 3px 8px rgba(0,0,0,.25);
    font-family: "Poppins", sans-serif;
  }
  .kicker {
    position: absolute;
    top: 58px;
    left: 0;
    width: 701px;
    display: flex;
    justify-content: center;
    align-items: center;
    gap: 10px;
  }
  .kicker .rule { width: 160px; height: 2px; background: var(--rule); }
  .kicker .word {
    font-family: "Playfair Display", serif;
    font-weight: 800;
    font-size: 60px;
    line-height: 1;
    color: var(--green);
    transform: scaleX(.72);
    margin: 0 -12px;
  }
  .title {
    margin: 0;
    padding: 0;
    font-size: inherit;
  }
  .title-line {
    position: absolute;
    left: 0;
    width: 701px;
    margin: 0;
    text-align: center;
    font-family: "Playfair Display", serif;
    font-weight: 800;
    font-size: 126px;
    line-height: 1;
    white-space: nowrap;
  }
  .title-line span { display: inline-block; transform: scaleX(.72); transform-origin: center; }
  .title-line.first { top: 106px; color: var(--green); }
  .title-line.second { top: 208px; color: var(--orange); }
  .subtitle {
    position: absolute;
    top: 336px;
    left: 0;
    width: 701px;
    text-align: center;
    font-weight: 600;
    font-size: 31px;
    line-height: 40px;
    color: var(--ink);
    margin: 0;
  }
  .hierarchy { position: absolute; left: 0; top: 0; }
  .bar-label {
    font-family: "Poppins", sans-serif;
    font-weight: 700;
    font-size: 26px;
    fill: #ffffff;
  }
  .author {
    position: absolute;
    top: 940px;
    left: 0;
    width: 701px;
    display: flex;
    justify-content: center;
    align-items: center;
    gap: 12px;
  }
  .author .rule { width: 80px; height: 2px; background: var(--rule); }
  .author .name {
    font-family: "Playfair Display", serif;
    font-weight: 700;
    font-size: 40px;
    letter-spacing: 1px;
    color: var(--green);
  }
</style>
</head>
<body>
  <main class="cover">
    <div class="kicker"><span class="rule"></span><span class="word">THE</span><span class="rule"></span></div>
    <h1 class="title">
      <span class="title-line first"><span>PLATE</span></span>
      <span class="title-line second"><span>COMPASS</span></span>
    </h1>
    <p class="subtitle">Cutting Through the Noise to<br>What Actually Works</p>

    <svg class="hierarchy" width="701" height="1052" viewBox="0 0 701 1052">
      <defs>
        <radialGradient id="plateTone" cx="50%" cy="50%" r="50%">
          <stop offset="0" stop-color="var(--plate-food)"/>
          <stop offset=".8" stop-color="var(--plate-mid)"/>
          <stop offset="1" stop-color="var(--plate-light)"/>
        </radialGradient>
      </defs>
      <g class="bars">
        <polygon points="150,467 521,467 488,527 150,527" fill="var(--noise)"/>
        <polygon points="150,538 600,538 567,598 150,598" fill="var(--supplements)"/>
        <polygon points="150,609 628,609 595,670 150,670" fill="var(--timing)"/>
        <polygon points="150,681 655,681 622,742 150,742" fill="var(--quality)"/>
        <polygon points="150,753 683,753 650,814 150,814" fill="var(--protein)"/>
        <polygon points="150,825 701,825 668,887 150,887" fill="var(--calories)"/>
      </g>
      <circle cx="158" cy="675" r="189" fill="var(--paper)"/>
      <g class="bar-labels">
        <text class="bar-label" x="363" y="506" text-anchor="middle">Noise</text>
        <text class="bar-label" x="373" y="578">Supplements</text>
        <text class="bar-label" x="393" y="650">Meal timing</text>
        <text class="bar-label" x="399" y="722">Food quality</text>
        <text class="bar-label" x="381" y="794">Protein</text>
        <text class="bar-label" x="330" y="866">Calories</text>
      </g>
      <path d="M158 465 A210 210 0 0 0 158 885" fill="none" stroke="var(--green)" stroke-width="2"/>
      <g class="arc" fill="none" stroke-width="22">
        <path d="M158 475 A200 200 0 0 1 258 502" stroke="var(--noise)"/>
        <path d="M260 503 A200 200 0 0 1 330 573" stroke="var(--supplements)"/>
        <path d="M332 577 A200 200 0 0 1 358 673" stroke="var(--timing)"/>
        <path d="M358 677 A200 200 0 0 1 339 758" stroke="var(--quality)"/>
        <path d="M338 762 A200 200 0 0 1 274 837" stroke="var(--protein)"/>
        <path d="M271 840 A200 200 0 0 1 158 875" stroke="var(--calories)"/>
      </g>
      <circle cx="166" cy="682" r="165" fill="url(#plateTone)" role="img" aria-label="Overhead photo of a plate with vegetables, fruit, nuts, cheese, bread and a fork"/>
    </svg>

    <div class="author"><span class="rule"></span><span class="name">MARA ELLISON</span><span class="rule"></span></div>
  </main>
</body>
</html>
```